TREVAL BUILDWORKS, LLC Webpage portfolio

I want to create a Website that allows my potential clients to browse my Skilled work via before and after photos. I want the website to enhance the work that I provide and potentially drive new business, or at least solidify my work.
I also do 3D CAD and Modeling of New Spaces and it would be nice to show some of that work from pencil design to 3D modeling, which I feel may help give me more clients.

The website needs to show a solid carpenter/company with the skills to get any project completed.

Types of Jobs - Custom Carpentry & Finishes, Kitchens, Baths, Basements, Decks, Porches, Whole House Renovation - Skilled Craftsmanship (Hardwood Flooring, Floor and Wall Tile) and much more...

Target Market(s)

Residential Home Renovation, Kitchen and Bath Renovation, Home Improvement

Industry/Entity Type

Residential Construction

Number of Pages Required

5+ page

Font styles to use
Sans Serif
Script

Requirements
Must have
• Similar to Plinvo.com, except for Treval Buildworks.
• Must be inviting.
• My Services Offered
• A way to reach me or contact me for estimates with some sort of Screening Questionare.
Nice to have
• Inviting Colors
Should not have
• Not sure at this time

```html
<!DOCTYPE html>
<html lang="en">
<head>
<meta charset="utf-8">
<title>Treval Buildworks</title>
<link href="https://fonts.googleapis.com/css2?family=Nunito+Sans:wght@400;600;700;800&display=swap" rel="stylesheet">
<style>
:root{
  --navy:#0d3d63;
  --blue:#27a0dd;
  --blue-dark:#1a86c4;
  --sky:#3fb4ec;
  --ink:#333a40;
  --muted:#8a9096;
  --line:#d9dcdf;
  --gray-band:#ececec;
  --footer:#eeeeee;
  --white:#ffffff;
  --link:#2398d6;
}
*{box-sizing:border-box;margin:0;padding:0}
html,body{width:1200px;height:3147px;overflow:hidden}
body{font-family:"Nunito Sans",Arial,sans-serif;color:var(--ink);background:var(--white);position:relative}
.abs{position:absolute}

/* header */
.site-header{left:0;top:0;width:1200px;height:111px}
.brand{left:147px;top:42px;display:flex;align-items:center;gap:9px;color:var(--navy);font-weight:800;font-size:21px;line-height:30px;white-space:nowrap}
.brand-mark{width:20px;height:20px;background:var(--navy);flex:none}
.search{left:394px;top:42px;width:477px;height:38px;border:2px solid var(--line);display:flex;align-items:center;padding-left:14px;gap:10px;color:#9aa0a5;font-size:14px}
.signup{left:948px;top:38px;display:flex;align-items:center;gap:10px;color:var(--navy);font-weight:600;font-size:17px}

.main-nav{left:0;top:111px;width:1200px;height:50px;background:linear-gradient(#37aee8,#1d8fcf);display:flex;padding-left:153px}
.main-nav a{color:var(--white);text-decoration:none;font-size:15px;line-height:50px;padding:0 25px;border-right:1px solid rgba(255,255,255,.35);letter-spacing:.3px}
.main-nav a.active{background:var(--navy)}

/* hero */
.hero{left:0;top:161px;width:1200px;height:473px;background:linear-gradient(100deg,#4a2c18 0%,#7a4a27 35%,#5a3720 60%,#b79b83 85%,#d8cdbf 100%)}
.hero-title{left:0;top:338px;width:1200px;text-align:center;color:var(--white);font-weight:800;font-size:36px;letter-spacing:1px}
.hero-sub{left:0;top:385px;width:1200px;text-align:center;color:var(--white);font-weight:700;font-size:28px;letter-spacing:.5px}
.btn-ghost{left:527px;top:443px;width:147px;height:40px;border:2px solid var(--white);color:var(--white);font-size:16px;display:flex;align-items:center;justify-content:center}
.dots{left:564px;top:588px;display:flex;gap:9px}
.dots span{width:14px;height:14px;border-radius:50%;background:var(--white)}
.dots span.on{background:transparent;border:2px solid var(--white)}

/* welcome */
.welcome-title{left:0;top:676px;width:1200px;text-align:center;font-size:30px;font-weight:600;color:#222}
.welcome-text{left:230px;top:727px;width:740px;text-align:center;font-size:17px;line-height:34px;color:var(--muted)}
.hex{width:256px;height:288px;clip-path:polygon(50% 0,100% 25%,100% 75%,50% 100%,0 75%,0 25%);display:flex;flex-direction:column;align-items:center;padding:48px 24px 0;text-align:center;color:var(--white)}
.hex h3{font-size:15px;font-weight:700;margin:18px 0 8px;white-space:nowrap}
.hex p{font-size:11.5px;line-height:17px;opacity:.85;padding:0 12px}
.hex-navy{left:204px;top:812px;background:var(--navy)}
.hex-blue{left:468px;top:812px;background:var(--blue)}
.hex-gray{left:732px;top:812px;background:#eaeaea;color:#444}
.hex-gray p{color:#999}

/* 3d modeling */
.modeling{left:0;top:1139px;width:1200px;height:418px;background:var(--gray-band)}
.section-title{width:1200px;text-align:center;font-size:28px;font-weight:600;color:#333}
.card{width:290px;background:var(--white);border:1px solid var(--line)}
.card .media{height:191px;width:100%}
.card .body{padding:14px 28px}
.card h4{color:var(--link);font-size:16px;font-weight:600;margin-bottom:6px}
.card p{font-size:11.5px;line-height:16px;color:#666}
.sketch{background:linear-gradient(135deg,#f3f4f5,#dadde0)}
.sketch-blue{background:linear-gradient(135deg,#eef5fa,#c8dde9)}

/* types of jobs */
.jobs{left:0;top:1557px;width:1200px;height:292px;background:var(--blue)}
.jobs-title{left:0;top:1592px;width:1200px;display:flex;justify-content:center;align-items:center;gap:22px;color:var(--white);font-size:28px}
.jobs-title i{display:block;width:38px;height:2px;background:var(--white)}
.job-list{left:196px;top:1670px;display:flex}
.job{display:flex;flex-direction:column;align-items:center;color:var(--white);font-size:14px;text-align:center;line-height:18px;padding:0 22px;border-right:1px solid rgba(255,255,255,.35);height:112px}
.job:last-child{border-right:none}
.job svg{height:56px;margin-bottom:14px}

/* projects */
.photo-card{width:288px;background:var(--white);border:1px solid var(--line)}
.photo-card .media{height:193px}
.photo-card .body{padding:12px 26px}
.photo-card h4{color:var(--link);font-size:16px;font-weight:600;margin-bottom:6px}
.photo-card p{font-size:11.5px;line-height:16px;color:#666}
.wood{background:linear-gradient(135deg,#8a5a34,#c89a63)}
.pale{background:linear-gradient(135deg,#e2ddd3,#a89a82)}
.teal{background:linear-gradient(135deg,#7e8c84,#a8b0a5)}
.amber{background:linear-gradient(135deg,#5b3a22,#c9965c)}
.feature{left:466px;top:2174px;width:581px;height:283px;background:linear-gradient(120deg,#4a2618,#b3562e 40%,#7a4e2e 70%,#2a2a30)}
.feature-cap{left:490px;top:2378px;color:var(--white)}
.feature-cap h4{font-size:16px;font-weight:600;margin-bottom:6px}
.feature-cap p{font-size:11.5px;line-height:16px;opacity:.9}

/* before after */
.ba-title{left:0;top:2494px;width:1200px;text-align:center;font-size:24px;font-weight:700;color:var(--navy)}
.ba-title span{color:var(--blue)}
.ba-rule{left:500px;top:2535px;width:200px;height:2px;background:var(--blue)}
.ba-rule-mark{left:583px;top:2533px;width:34px;height:5px;background:var(--navy)}
.ba{width:286px;height:151px;display:flex;position:absolute}
.ba .half{flex:1;position:relative}
.ba .half span{position:absolute;bottom:0;left:0;right:0;height:22px;background:rgba(0,0,0,.55);color:var(--white);font-size:13px;line-height:22px;text-align:center;letter-spacing:.5px}

/* footer */
.site-footer{left:0;top:2797px;width:1200px;height:281px;background:var(--footer)}
.foot-col{top:2852px}
.foot-col h5{font-size:17px;font-weight:600;color:#333;margin-bottom:16px;letter-spacing:.3px}
.foot-col li{list-style:none;font-size:13px;color:#777;line-height:23px}
.foot-brand{left:835px;top:2880px;color:var(--navy);font-weight:800;font-size:22px;display:flex;align-items:center;gap:9px;white-space:nowrap}
.social{left:845px;top:2963px;display:flex;gap:12px}
.social span{width:33px;height:33px;border-radius:50%;background:var(--blue)}
.copyright{left:0;top:3104px;width:1200px;text-align:center;font-size:12px;color:#777}
.foot-rule{left:0;top:3078px;width:1200px;height:1px;background:var(--line)}
</style>
</head>
<body>

<header class="site-header abs">
  <div class="brand abs"><span class="brand-mark"></span>Treval Buildworks</div>
  <div class="search abs">
    <svg width="16" height="16" viewBox="0 0 16 16"><circle cx="6.5" cy="6.5" r="5" fill="none" stroke="#9aa0a5" stroke-width="2"/><path d="M10.5 10.5 15 15" stroke="#9aa0a5" stroke-width="2"/></svg>
    Search Photos, Product Etc
  </div>
  <div class="signup abs">
    <svg width="32" height="32" viewBox="0 0 32 32"><circle cx="16" cy="16" r="14.5" fill="none" stroke="#0d3d63" stroke-width="2"/><circle cx="16" cy="12" r="5" fill="#0d3d63"/><path d="M7 25c2-5 16-5 18 0" fill="#0d3d63"/></svg>
    Sign Up
  </div>
</header>

<nav class="main-nav abs">
  <a class="active">HOME</a><a>ABOUT US</a><a>WHAT WE DO</a><a>DEPARTMENT</a><a>SALE</a><a>PHOTOS</a><a>RESOURCES</a>
</nav>

<section class="hero abs" role="img" aria-label="Photo of a renovated kitchen with dark wood cabinets and pendant lights"></section>
<h1 class="hero-title abs">PRAESENT ELEMENTUM ELIT AT TELLUS</h1>
<p class="hero-sub abs">ETIAM EU URNA PORTA SUSPENDISSE</p>
<div class="btn-ghost abs">Get Started</div>
<div class="dots abs"><span class="on"></span><span></span><span></span><span></span></div>

<h2 class="welcome-title abs">Welcome to Treval Buildworks</h2>
<p class="welcome-text abs">Praesent elementum elit at tellus nec ultricies sit amet porttitor mattis enim In massa libero interdum nec interdum vel blandit sed nulla In ullamcorper est eget</p>

<div class="hex hex-navy abs">
  <svg width="66" height="70" viewBox="0 0 66 70" fill="none" stroke="#fff" stroke-width="3"><circle cx="33" cy="18" r="13"/><path d="M6 68c0-18 10-28 27-28s27 10 27 28z"/><path d="M33 42l-4 8 4 14 4-14z"/></svg>
  <h3>Find Home Professionals</h3>
  <p>Class aptent taciti sociosqu ad litora torquent per conubia nostra per inceptos hymenaeos</p>
</div>
<div class="hex hex-blue abs">
  <svg width="66" height="70" viewBox="0 0 66 70" fill="none" stroke="#fff" stroke-width="3" stroke-linejoin="round"><path d="M8 30 36 6h24L32 30z"/><path d="M8 30v34h24V30"/><path d="M32 64l28-24V6"/></svg>
  <h3>3D CAD and Modeling</h3>
  <p>Class aptent taciti sociosqu ad litora torquent per conubia nostra per inceptos hymenaeos</p>
</div>
<div class="hex hex-gray abs">
  <svg width="84" height="70" viewBox="0 0 84 70" fill="#888"><rect x="6" y="40" width="50" height="14" rx="3"/><rect x="10" y="30" width="42" height="12" rx="3"/><rect x="4" y="54" width="4" height="6"/><rect x="54" y="54" width="4" height="6"/><path d="M66 22h14l-3-12h-8z"/><rect x="72" y="22" width="2" height="34"/><rect x="66" y="56" width="14" height="3"/></svg>
  <h3>Shop for Your Home</h3>
  <p>Class aptent taciti sociosqu ad litora torquent per conubia nostra per inceptos hymenaeos</p>
</div>

<section class="modeling abs">
  <h2 class="section-title abs" style="top:35px">3D Modeling</h2>
  <article class="card abs" style="left:147px;top:89px">
    <div class="media sketch" role="img" aria-label="3D wireframe model of a house interior"></div>
    <div class="body"><h4>Home/Project Tittle</h4><p>Praesent elementum elit at tellus nec ultricies sit amet porttitor mattis enim In</p></div>
  </article>
  <article class="card abs" style="left:447px;top:89px">
    <div class="media sketch" role="img" aria-label="3D wireframe model of a room layout"></div>
    <div class="body"><h4>Home/Project Tittle</h4><p>Praesent elementum elit at tellus nec ultricies sit amet porttitor mattis enim In</p></div>
  </article>
  <article class="card abs" style="left:747px;top:89px">
    <div class="media sketch-blue" role="img" aria-label="Blue 3D wireframe model of a house"></div>
    <div class="body"><h4>Home/Project Tittle</h4><p>Praesent elementum elit at tellus nec ultricies sit amet porttitor mattis enim In</p></div>
  </article>
</section>

<section class="jobs abs"></section>
<h2 class="jobs-title abs"><i></i>Types of Jobs<i></i></h2>
<div class="job-list abs">
  <div class="job"><svg viewBox="0 0 50 56" width="50" fill="none" stroke="#fff" stroke-width="3"><path d="M6 10l14-6 10 6-6 6-8-4z"/><path d="M20 14l24 36"/></svg>Custom Carpentry &amp;<br>Finishes, Kitchen</div>
  <div class="job"><svg viewBox="0 0 50 56" width="50" fill="none" stroke="#fff" stroke-width="3"><path d="M4 30h42v8c0 8-6 12-12 12H16C10 50 4 46 4 38z"/><path d="M12 30V10c0-4 8-4 8 0"/><path d="M26 10h16v8H26z"/></svg>Baths</div>
  <div class="job"><svg viewBox="0 0 50 56" width="50" fill="none" stroke="#fff" stroke-width="3"><rect x="4" y="6" width="42" height="44"/><path d="M14 50V36h10V26h10V16h8" /></svg>Basements</div>
  <div class="job"><svg viewBox="0 0 40 56" width="36" fill="none" stroke="#fff" stroke-width="3"><rect x="4" y="4" width="32" height="48"/><path d="M10 16h20M10 26h20M10 36h20"/></svg>Decks</div>
  <div class="job"><svg viewBox="0 0 44 56" width="40" fill="none" stroke="#fff" stroke-width="3"><path d="M4 20l8-14 8 14v32H4z"/><path d="M24 20l8-14 8 14v32H24z"/></svg>Porches</div>
  <div class="job"><svg viewBox="0 0 50 56" width="48" fill="none" stroke="#fff" stroke-width="3"><rect x="4" y="4" width="36" height="14" rx="2"/><path d="M40 11h6v14H24v8"/><rect x="20" y="33" width="8" height="20"/></svg>Whole House<br>Renovation</div>
  <div class="job"><svg viewBox="0 0 60 56" width="58" fill="none" stroke="#fff" stroke-width="3"><path d="M10 14h44L48 48H4z"/><path d="M20 14l-8 34M32 14l-6 34M44 14l-6 34M8 30h42"/></svg>Hardwood<br>Flooring</div>
</div>

<article class="photo-card abs" style="left:159px;top:1872px">
  <div class="media pale" role="img" aria-label="Photo of a remodeled hallway with white doors"></div>
  <div class="body"><h4>Home/Project Tittle</h4><p>Praesent elementum elit at tellus nec ultricies sit amet porttitor mattis enim In</p></div>
</article>
<article class="photo-card abs" style="left:459px;top:1872px">
  <div class="media wood" role="img" aria-label="Photo of a kitchen with wood cabinets and granite counters"></div>
  <div class="body"><h4>Home/Project Tittle</h4><p>Praesent elementum elit at tellus nec ultricies sit amet porttitor mattis enim In</p></div>
</article>
<article class="photo-card abs" style="left:759px;top:1872px">
  <div class="media teal" role="img" aria-label="Photo of a kitchen with a teal island"></div>
  <div class="body"><h4>Home/Project Tittle</h4><p>Praesent elementum elit at tellus nec ultricies sit amet porttitor mattis enim In</p></div>
</article>
<article class="photo-card abs" style="left:159px;top:2174px">
  <div class="media amber" role="img" aria-label="Photo of a finished basement room with recessed lights"></div>
  <div class="body"><h4>Home/Project Tittle</h4><p>Praesent elementum elit at tellus nec ultricies sit amet porttitor mattis enim In</p></div>
</article>
<div class="feature abs" role="img" aria-label="Photo of a kitchen with a granite island and dining chairs"></div>
<div class="feature-cap abs"><h4>Project Tittle</h4><p>Praesent elementum elit at tellus nec ultricies<br>sit amet porttitor mattis enim In</p></div>

<h2 class="ba-title abs">BEFORE <span>&amp; AFTER</span></h2>
<div class="ba-rule abs"></div><div class="ba-rule-mark abs"></div>

<div class="ba" style="left:145px;top:2564px">
  <div class="half" style="background:linear-gradient(135deg,#9a968c,#4c4a44)" role="img" aria-label="Porch before renovation"><span>BEFORE</span></div>
  <div class="half" style="background:linear-gradient(135deg,#6b5b4a,#2e2a26)" role="img" aria-label="Porch after renovation"><span>AFTER</span></div>
</div>
<div class="ba" style="left:457px;top:2564px">
  <div class="half" style="background:linear-gradient(135deg,#c0652e,#6a3c22)" role="img" aria-label="Kitchen before renovation"><span>BEFORE</span></div>
  <div class="half" style="background:linear-gradient(135deg,#7a4a2a,#3a2418)" role="img" aria-label="Kitchen after renovation"><span>AFTER</span></div>
</div>
<div class="ba" style="left:770px;top:2564px">
  <div class="half" style="background:linear-gradient(135deg,#3a2a20,#6a4a32)" role="img" aria-label="Wall before refinishing"><span>BEFORE</span></div>
  <div class="half" style="background:linear-gradient(135deg,#a06a3a,#d09a62)" role="img" aria-label="Wall after refinishing"><span>AFTER</span></div>
</div>

<footer class="site-footer abs"></footer>
<div class="foot-col abs" style="left:147px"><h5>COMPANY</h5><ul><li>Home</li><li>About Us</li><li>What We Do</li><li>Our Services</li></ul></div>
<div class="foot-col abs" style="left:319px"><h5>OUR SERVICES</h5><ul><li>Custom Carpentry</li><li>Finishes</li><li>Kitchens</li><li>Baths</li><li>Basements</li></ul></div>
<div class="foot-col abs" style="left:476px"><h5>&nbsp;</h5><ul><li>Decks</li><li>Porches</li><li>Whole House Renovation</li><li>Craftsmanship</li></ul></div>
<div class="foot-col abs" style="left:680px"><h5>RESOURCES</h5><ul><li>Support</li><li>Testimonials</li><li>Contact Us</li><li>Term of Use</li></ul></div>
<div class="foot-brand abs"><span class="brand-mark"></span>Treval Buildworks</div>
<div class="social abs"><span></span><span></span><span></span><span></span></div>
<div class="foot-rule abs"></div>
<p class="copyright abs">© 2017 Company Name &nbsp;All right reserved &nbsp;Term of Use</p>

</body>
</html>
```